Maplecrest Disability - Social Security Disability Attorneys

Our company is expanding to attract clients nationwide for our social security disability practice. We have a logo, but I am looking for a creative and elegant letterhead that projects an image of being technologically advanced but still professional enough for the legal field. I am looking for the "wow factor" combined with this is still professional enough for a law practice.

Requesting letterhead and business card design
Updates

Had to update and change the logo. The previous logo had a typo. Please send updates with the new logo for consideration. The letterhead and business cards should be professional enough to be used for a law firm. Thanks.

Industry/Entity Type

Law Practice, Law Firm, Healthcare Industry, Government

Colors

Designer to choose colors to be used in the design.

Requirements
Nice to have
• **Please create a vertical design for the business card**

```html
<!DOCTYPE html>
<html lang="en">
<head>
<meta charset="utf-8">
<title>Maplecrest Disability – Letterhead</title>
<link rel="stylesheet" href="https://fonts.googleapis.com/css2?family=Lato:wght@400;700&display=swap">
<style>
  :root {
    --backdrop: #e6e6e6;
    --paper: #ffffff;
    --ink: #262626;
    --accent: #f07a1e;
    --signature-tone: #ececec;
  }
  * { box-sizing: border-box; margin: 0; padding: 0; }
  html, body {
    width: 1200px; height: 1200px; overflow: hidden;
    background: var(--backdrop);
    font-family: "Lato", Arial, sans-serif;
    color: var(--ink);
  }
  .letterhead {
    position: absolute; left: 248px; top: 77px;
    width: 721px; height: 1045px;
    background: var(--paper);
  }
  .brand-name {
    position: absolute; left: 41px; top: 92px;
    font-size: 20px; font-weight: 700; line-height: 24px;
    color: var(--ink);
  }
  .contact {
    position: absolute; left: 520px; top: 55px;
    font-size: 12px; line-height: 17px; font-style: normal;
  }
  .contact-address { margin-bottom: 6px; }
  .contact-line { display: flex; align-items: center; gap: 7px; line-height: 18px; }
  .contact-line svg { width: 11px; height: 11px; flex: none; }
  .letter-date, .recipient, .salutation, .letter-body, .closing, .signature {
    position: absolute; left: 41px;
  }
  .letter-date { top: 218px; font-size: 15px; line-height: 18px; }
  .recipient { font-size: 14px; line-height: 17px; }
  .recipient-person { top: 254px; }
  .recipient-company { top: 307px; }
  .salutation { top: 379px; font-size: 17px; font-weight: 700; line-height: 22px; }
  .letter-body { top: 421px; width: 640px; font-size: 13.6px; line-height: 16.4px; }
  .body-text { text-align: justify; margin-bottom: 16.4px; }
  .closing { top: 718px; font-size: 14px; line-height: 18px; }
  .signature {
    top: 760px; width: 186px; height: 38px;
    background: var(--signature-tone); border-radius: 4px;
  }
</style>
</head>
<body>
  <main class="letterhead">
    <header>
      <div class="brand-name">Maplecrest Disability</div>
      <address class="contact">
        <div class="contact-address">Suite 4, Level 12, Harbour Lane<br>Carlton VIC 3053</div>
        <div class="contact-line">
          <svg viewBox="0 0 12 12"><path d="M2.5 1 L4.5 1 L5.3 3.6 L4 4.6 Q5 7 7.4 8 L8.4 6.7 L11 7.5 L11 9.5 Q10.5 11 9 11 Q1 10 1 2.5 Q1 1 2.5 1Z" fill="var(--accent)"/></svg>
          <span>555-014-2270</span>
        </div>
        <div class="contact-line">
          <svg viewBox="0 0 12 12"><rect x="0.5" y="2" width="11" height="8" rx="1" fill="var(--accent)"/><path d="M1 2.6 L6 6.5 L11 2.6" fill="none" stroke="#fff" stroke-width="1"/></svg>
          <span>info@maplecrestdisability.com</span>
        </div>
        <div class="contact-line">
          <svg viewBox="0 0 12 12"><circle cx="6" cy="6" r="5.3" fill="var(--accent)"/><path d="M0.8 6 H11.2 M6 0.7 Q2.8 6 6 11.3 M6 0.7 Q9.2 6 6 11.3" fill="none" stroke="#fff" stroke-width="0.8"/></svg>
          <span>www.maplecrestdisability.com</span>
        </div>
      </address>
    </header>

    <p class="letter-date">January-03-2020</p>
    <p class="recipient recipient-person">Mr, Peter Lindqvist<br>President</p>
    <p class="recipient recipient-company">Northgate Holdings<br>48 Alder Road, Suite# 6<br>City, State, 120023</p>
    <p class="salutation">Dear Mr, Peter</p>
    <section class="letter-body">
      <p class="body-text">Lorem ipsum dolor sit amet, consectetur adipisicing elit, sed do eiusmod tempor incididunt ut labore et dolore magna aliqua. Ut enim ad minim veniam, quis nostrud exercitation ullamco laboris nisi ut aliquip ex ea commodo consequat. Duis aute irure dolor in reprehenderit in voluptate velit esse cillum dolore eu fugiat nulla pariatur.</p>
      <p class="body-text">Lorem ipsum dolor sit amet, consectetur adipisicing elit, sed do eiusmod tempor incididunt ut labore et dolore magna aliqua. Ut enim ad minim veniam, quis nostrud exercitation ullamco laboris nisi ut aliquip ex ea commodo consequat. Duis aute irure dolor in reprehenderit in voluptate velit esse cillum dolore eu fugiat nulla pariatur.</p>
      <p class="body-text">Lorem ipsum dolor sit amet, consectetur adipisicing elit, sed do eiusmod tempor incididunt ut labore et dolore magna aliqua. Ut enim ad minim veniam, quis nostrud exercitation ullamco laboris nisi ut aliquip ex ea commodo consequat.</p>
      <p class="body-text">Excepteur sint occaecat cupidatat non proident, sunt in culpa qui officia deserunt mollit anim id est laborum. re et dolore magnam aliquam quaerat voluptatem.</p>
    </section>
    <p class="closing">Regards</p>
    <div class="signature" role="img" aria-label="Handwritten signature of Daniel Whitford"></div>
  </main>
</body>
</html>
```